Redesign current business card for food company

i would like to redesign my business card. our company is food company, our product range from chips, juices, milk and etc (mostly dried food stuff).
I want o keep same logo but , the rest is open to new design.
you can check at our website about our company www.orvelpantry.com

Target Market(s)

most of food company

Industry/Entity Type

Business

Contact Information for Business Card

I want to keep more to blue color...

Colors
3176b5
abd036

Requirements
Must have
• our old logo
Nice to have
• we do not mind to have nice material on bus card in order to accomplish nice design. for example: using spot uv, embossed and etc.

```html
<!DOCTYPE html>
<html lang="en">
<head>
<meta charset="utf-8">
<title>Orvel Pantry – Business Card</title>
<link rel="stylesheet" href="https://fonts.googleapis.com/css2?family=PT+Sans:wght@400;700&display=swap">
<style>
  :root {
    --page-bg: #e9e6e1;
    --sun-deep: #f7a21b;
    --sun-light: #fdd41d;
    --sun-band-a: #fee51a;
    --sun-band-b: #fbbd1c;
    --brand-blue: #1b67b8;
    --sky-top: #1a92d6;
    --sky-bottom: #1c5ea8;
    --sea-band-a: #0a3fd8;
    --sea-band-b: #1580d8;
    --ink-light: #ffffff;
    --card-shadow: 0 10px 24px rgba(40, 30, 20, 0.25);
  }
  * { box-sizing: border-box; margin: 0; padding: 0; }
  html, body {
    width: 1200px; height: 900px; overflow: hidden;
    background: var(--page-bg);
    font-family: "PT Sans", "Helvetica Neue", Arial, sans-serif;
  }
  .card {
    position: absolute;
    width: 560px; height: 320px;
    overflow: hidden;
    box-shadow: var(--card-shadow);
  }
  .tone-band {
    position: absolute; top: 0; bottom: 0; left: 0;
    width: 190px;
  }

  /* front */
  .card-front {
    left: 70px; top: 110px;
    background: linear-gradient(200deg, var(--sun-deep) 0%, #fbb81c 45%, var(--sun-light) 100%);
  }
  .card-front .tone-band {
    background: linear-gradient(90deg, var(--sun-band-a) 0%, var(--sun-band-b) 100%);
  }
  .front-brand {
    position: absolute; left: 240px; top: 82px;
    text-align: center;
  }
  .front-brand .wordmark {
    font-weight: 700; font-size: 86px; line-height: 1;
    color: var(--brand-blue); letter-spacing: -1px;
  }
  .front-brand .website {
    margin-top: 8px;
    font-size: 13px; color: var(--brand-blue);
  }

  /* back */
  .card-back {
    left: 570px; top: 470px;
    background: linear-gradient(170deg, var(--sky-top) 0%, var(--sky-bottom) 100%);
    color: var(--ink-light);
  }
  .card-back .tone-band {
    background: linear-gradient(90deg, var(--sea-band-a) 0%, var(--sea-band-b) 100%);
  }
  .back-brand {
    position: absolute; left: 262px; top: 20px;
    font-weight: 700; font-size: 70px; line-height: 1;
    color: var(--ink-light); letter-spacing: -1px;
  }
  .holder { position: absolute; left: 270px; top: 112px; }
  .holder-name { font-weight: 700; font-size: 17px; }
  .holder-role { font-size: 13px; margin-top: 1px; }
  .contact-list {
    position: absolute; left: 274px; top: 168px;
    list-style: none; font-size: 14px;
  }
  .contact-list li { display: flex; align-items: center; height: 20px; }
  .contact-list svg { width: 11px; height: 11px; margin-right: 7px; fill: var(--ink-light); }
  .address {
    position: absolute; left: 290px; top: 266px;
    font-size: 14px;
  }
</style>
</head>
<body>

<section class="card card-front">
  <div class="tone-band"></div>
  <div class="front-brand">
    <div class="wordmark">orvel</div>
    <div class="website">www.orvelpantry.com</div>
  </div>
</section>

<section class="card card-back">
  <div class="tone-band"></div>
  <div class="back-brand">orvel</div>
  <div class="holder">
    <div class="holder-name">Daniel Hartono</div>
    <div class="holder-role">President</div>
  </div>
  <ul class="contact-list">
    <li><svg viewBox="0 0 12 12"><path d="M1,4 C1,2 3,1 6,1 C9,1 11,2 11,4 L8.5,4.5 L8,3 L4,3 L3.5,4.5 Z M3,6 L9,6 L10.5,11 L1.5,11 Z"/></svg>555 210 4418</li>
    <li><svg viewBox="0 0 12 12"><path d="M3,1 L9,1 L9,4 L11,4 L11,10 L9,10 L9,11 L3,11 L3,10 L1,10 L1,4 L3,4 Z M4,2 L4,4 L8,4 L8,2 Z M4,8 L4,10 L8,10 L8,8 Z"/></svg>555 210 4419</li>
    <li><svg viewBox="0 0 12 12"><path d="M3.5,0.5 L8.5,0.5 L8.5,11.5 L3.5,11.5 Z M4.5,2 L4.5,9 L7.5,9 L7.5,2 Z"/></svg>555 387 2914</li>
    <li><svg viewBox="0 0 12 12"><path d="M0.5,2.5 L11.5,2.5 L6,7 Z M0.5,4 L6,8.5 L11.5,4 L11.5,10 L0.5,10 Z"/></svg>daniel@orvelpantry.com</li>
  </ul>
  <div class="address">2140 W Linden St.Harwick CA 90412</div>
</section>

</body>
</html>
```